Forensic Document Examiner, looking for contemporary update to my stationery design.

Looking for professional, classy logo design for stationery and business cards. My current stationery and business card is attached.I believe a logo image makes a header section interesting, so an intriguing design of a pen, feathered pen, microscope, magnifying glass, etc., would be appropriate. I have been in the business for over 30 years. I leave ideas to the imagination of the designer.My work involves mainly, the comparison of signatures and handwriting. I also resolve alterations, obliterations, and work as shown on my website: www.documentexaminer.infoThe image produced will be printed on quality white stationery and envelopes. The stationery will be photocopied by my clients, so the images should be reproducible. The business cards may be designed in other than white.

Target Market(s)

Attorneys

Font styles to use
Sans Serif

Colors

Designer to choose colors to be used in the design.

Requirements
Must have
• Image suitable for white stationery and photocopying.
• Classy logo and image; no casual fonts.
Nice to have
• Intriguing, contemporary design incorporating a relevant logo to my work.

```html
<!DOCTYPE html>
<html lang="en">
<head>
<meta charset="utf-8">
<title>Daniel R. Whitlow – Business Card</title>
<link rel="stylesheet" href="https://fonts.googleapis.com/css2?family=Arvo&family=Open+Sans:ital,wght@0,400;1,400&family=Fira+Sans+Condensed:wght@600&display=swap">
<style>
  :root {
    --page-bg: #e6e4e1;
    --card-top: #2e2e2e;
    --card-bottom: #232323;
    --gold: #c9ad1e;
    --icon-gold: #b9a326;
    --text-light: #d6d6d6;
    --text-muted: #bdbdbd;
    --white: #f4f4f4;
    --art-light: #d9d9d9;
    --art-dark: #8a8a8a;
  }
  * { margin: 0; padding: 0; box-sizing: border-box; }
  html, body {
    width: 1125px; height: 1200px; overflow: hidden;
    background: var(--page-bg);
    font-family: "Open Sans", sans-serif;
  }
  .card {
    position: absolute;
    left: 155px; width: 826px; height: 470px;
    border-radius: 22px;
    background: linear-gradient(135deg, var(--card-top), var(--card-bottom));
    overflow: hidden;
  }
  .card--front { top: 100px; }
  .card--back { top: 632px; }

  .front-art {
    position: absolute; left: 21px; top: 11px; width: 330px; height: 442px;
    background: radial-gradient(ellipse at 40% 55%, var(--art-light) 0%, var(--art-dark) 55%, rgba(60,60,60,0) 80%);
    opacity: .55;
  }
  .contact {
    position: absolute; right: 59px; top: 226px;
    text-align: right;
  }
  .contact__name {
    font-family: "Arvo", serif; font-size: 28px; color: var(--gold);
    line-height: 1.1;
  }
  .contact__title { font-size: 19px; color: var(--text-light); margin-top: 6px; }
  .contact__list { list-style: none; margin-top: 16px; }
  .contact__item {
    font-size: 17px; color: var(--text-muted); line-height: 25px;
    display: flex; justify-content: flex-end; align-items: center; gap: 8px;
  }
  .contact__item svg { width: 16px; height: 16px; fill: var(--icon-gold); }
  .contact__address { font-size: 17px; color: var(--text-muted); margin-top: 14px; margin-right: 0; }

  .brand {
    position: absolute; left: 180px; top: 140px;
    display: flex; align-items: center; gap: 22px;
  }
  .brand__mark {
    width: 96px; height: 96px; border-radius: 50%;
    background: var(--art-light); opacity: .85; flex: none;
  }
  .brand__name {
    font-family: "Open Sans", sans-serif; font-weight: 400;
    color: var(--white); line-height: 1; letter-spacing: 3px;
  }
  .brand__name-first { display: block; font-size: 46px; }
  .brand__name-last { display: block; font-size: 64px; margin-top: 6px; }
  .brand__tagline {
    position: absolute; left: 300px; top: 262px;
    font-family: "Fira Sans Condensed", sans-serif; font-weight: 600;
    font-size: 25px; color: var(--gold);
  }
  .services {
    position: absolute; left: 0; right: 0; top: 370px;
    text-align: center; font-style: italic; font-size: 17.5px;
    line-height: 25px; color: var(--text-muted);
  }
</style>
</head>
<body>
  <section class="card card--front">
    <div class="front-art" role="img" aria-label="Large illustration of a laboratory microscope"></div>
    <div class="contact">
      <h1 class="contact__name">Daniel R. Whitlow</h1>
      <p class="contact__title">Forensic document Examiner</p>
      <ul class="contact__list">
        <li class="contact__item">(888) 555-0147
          <svg viewBox="0 0 16 16" aria-hidden="true"><path d="M3.2 1.5l2.4 2.6-1.3 2a9 9 0 0 0 5.6 5.6l2-1.3 2.6 2.4-1.3 2C7 14.6 1.4 9 1.2 2.8z"/></svg>
        </li>
        <li class="contact__item">dwhitlow@quillmarkreview.info
          <svg viewBox="0 0 16 16" aria-hidden="true"><path d="M1 3.5h14v9H1z M1.6 4l6.4 5 6.4-5" fill="var(--icon-gold)"/><path d="M1.5 4l6.5 5 6.5-5" fill="none" stroke="#2a2a2a" stroke-width="1.2"/></svg>
        </li>
        <li class="contact__item">www.quillmarkreview.info
          <svg viewBox="0 0 16 16" aria-hidden="true"><circle cx="8" cy="8" r="7"/><path d="M5 4.5c1.5 0 2.5 1 2 2.5S4 8 4.5 10s2 1.5 2 3M10 3c0 1.5 1 2 2.5 2M11 9c1 .5 1 2 .5 3" fill="none" stroke="#2a2a2a" stroke-width="1.3"/></svg>
        </li>
      </ul>
      <p class="contact__address">P.O.Box 2840, Salem, OR 97301</p>
    </div>
  </section>

  <section class="card card--back">
    <div class="brand">
      <span class="brand__mark" aria-hidden="true"></span>
      <p class="brand__name">
        <span class="brand__name-first">DANIEL R.</span>
        <span class="brand__name-last">WHITLOW</span>
      </p>
    </div>
    <p class="brand__tagline">Forensic Document Examiner</p>
    <p class="services">Full service laboratory, Specializing in handwriting comparisons,<br>obliterations, alterations indented wrinting recovery, etc.</p>
  </section>
</body>
</html>
```